Business Card Design Can you design a business card design? Looking for something unique and differe

Can you design a business card design? Looking for something unique and different. Can you design a business card design? Looking for something unique and different.Can you design a business card design? Looking for something unique and different.Can you design a business card design? Looking for something unique and different.Can you design a business card design? Looking for something unique and different.Can you design a business card design? Looking for something unique and different.

Industry/Entity Type

Business

Contact Information for Business Card

Can you design a business card design? Looking for something unique and different.

Font styles to use
Serif

```html
<!DOCTYPE html>
<html lang="en">
<head>
<meta charset="utf-8">
<title>Remedia Business Card</title>
<link href="https://fonts.googleapis.com/css2?family=Open+Sans:wght@400;600&display=swap" rel="stylesheet">
<style>
  :root {
    --backdrop: #d9d9d9;
    --card: #ffffff;
    --plum: #8a6b9c;
    --ink: #2b2b2b;
    --muted: #555555;
    --icon: #6f6f6f;
  }
  * { margin: 0; padding: 0; box-sizing: border-box; }
  html, body {
    width: 1200px; height: 852px; overflow: hidden;
    background: var(--backdrop);
    font-family: "Open Sans", Arial, sans-serif;
  }
  .stage {
    width: 1200px; height: 852px;
    display: flex; align-items: center; justify-content: center; gap: 40px;
  }
  .card {
    position: relative;
    width: 525px; height: 300px;
    background: var(--card);
    border-radius: 12px;
    box-shadow: 0 4px 14px rgba(0,0,0,0.12);
    overflow: hidden;
  }
  /* Front */
  .card--front {
    display: flex; align-items: center; justify-content: center;
  }
  .brand {
    display: flex; align-items: center; gap: 14px;
    color: var(--plum); font-weight: 600;
  }
  .brand__square {
    width: 22px; height: 22px; background: var(--plum);
  }
  .brand__name { font-size: 46px; letter-spacing: 1px; }

  /* Back */
  .card--back .brand {
    position: absolute; left: 40px; top: 128px;
  }
  .card--back .brand__name { font-size: 36px; }
  .card--back .brand__square { width: 18px; height: 18px; }
  .holder {
    position: absolute; left: 300px; top: 58px;
  }
  .holder__name {
    color: var(--plum); font-weight: 600; font-size: 17px;
  }
  .holder__title {
    color: var(--ink); font-size: 10px; margin-top: 2px;
  }
  .contact {
    position: absolute; left: 300px; top: 140px;
    list-style: none; font-size: 12px; color: var(--ink);
  }
  .contact li {
    display: flex; align-items: center; gap: 8px; height: 19px;
  }
  .contact svg { width: 11px; height: 11px; fill: var(--icon); flex: none; }
  .address {
    position: absolute; left: 300px; top: 210px;
    font-size: 12px; line-height: 17px; color: var(--ink);
  }
</style>
</head>
<body>
<main class="stage">
  <section class="card card--front">
    <div class="brand">
      <span class="brand__square"></span>
      <span class="brand__name">Remedia</span>
    </div>
  </section>

  <section class="card card--back">
    <div class="brand">
      <span class="brand__square"></span>
      <span class="brand__name">Remedia</span>
    </div>

    <div class="holder">
      <p class="holder__name">Your Long Name</p>
      <p class="holder__title">Managing Director</p>
    </div>

    <ul class="contact">
      <li>
        <svg viewBox="0 0 12 12" aria-hidden="true"><path d="M2 1h2.5l1 3-1.5 1a7 7 0 0 0 3 3l1-1.5 3 1V10a1 1 0 0 1-1 1A10 10 0 0 1 1 2a1 1 0 0 1 1-1z"/></svg>
        00.00.00.0000
      </li>
      <li>
        <svg viewBox="0 0 12 12" aria-hidden="true"><path d="M0 2h12v8H0z M1 3l5 3.5L11 3" fill="none" stroke="#6f6f6f" stroke-width="1.2"/></svg>
        yourname@yourwebsite.com
      </li>
      <li>
        <svg viewBox="0 0 12 12" aria-hidden="true"><circle cx="6" cy="6" r="5" fill="none" stroke="#6f6f6f" stroke-width="1.2"/><path d="M1 6h10M6 1c-2.5 3-2.5 7 0 10M6 1c2.5 3 2.5 7 0 10" fill="none" stroke="#6f6f6f" stroke-width="1"/></svg>
        www.yourwebsite.com
      </li>
    </ul>

    <p class="address">Your Commercial or office address<br>in just two line with pincode</p>
  </section>
</main>
</body>
</html>
```